Audio/ Video Packaging Design for a Technology company.

We need a packaging design for a bag that is 7" wide and 10" high. The design will be for a new line of audio/video products. We would like to see designs that represent a superior quality product that provides a pure connection. We want the equivalent of a nice retail bag that you would find in a store like Tallow Mart. It should be a maximum of three colors. We really want something sharp, professional and eye catching, not whimsical or cartoonish. I've included a couple of examples below. I don't really like the designs of the bags, but I want you to see examples of what I'm looking for.

The company logo, which is uploaded, should be on the design. The words "audio and video products" should be either underneath the logo or to the side. Also, somewhere on the bag, we would like the words "For a Pure Connection"

The winner of this contest will likely get the opportunity for additional work as we have more products ready to launch.

Target Market(s)

resellers, consumers - men 25-60

Industry/Entity Type

It Company

Requirements
Must have
• It should be a maximum of three colors. We really want something sharp, professional and eye catching, not whimsical or cartoonish
Nice to have
• Eye-catching design. Utilize the entire bag but don't make it too busy.
Should not have
• Whimsical, cartoonish

```html
<!DOCTYPE html>
<html lang="en">
<head>
<meta charset="utf-8">
<title>Veloria Audio and Video Products – Bag Packaging</title>
<link rel="stylesheet" href="https://fonts.googleapis.com/css2?family=Questrial&family=PT+Sans+Narrow:wght@700&display=swap">
<style>
  :root {
    --backdrop: #fbe3a6;
    --orange: #fbb22a;
    --orange-deep: #f5a012;
    --orange-pale: #fde7ad;
    --cream: #fff6dc;
    --white: #ffffff;
    --ink: #2a2418;
    --seal-line: rgba(255, 255, 255, 0.55);
  }
  * { box-sizing: border-box; margin: 0; padding: 0; }
  html, body { width: 1200px; height: 787px; overflow: hidden; }
  body {
    background: var(--backdrop);
    position: relative;
    font-family: "Questrial", sans-serif;
  }

  .bag {
    position: absolute;
    top: 118px;
    width: 428px;
    height: 612px;
    border-radius: 26px;
    background: linear-gradient(90deg, var(--orange-deep), var(--orange) 45%, var(--orange-deep));
    overflow: hidden;
  }
  .bag--front { left: 154px; }
  .bag--back  { left: 618px; }

  .bag__panel {
    position: absolute;
    left: 20px;
    top: 20px;
    width: 388px;
    border-radius: 22px;
  }
  .bag--front .bag__panel {
    height: 542px;
    background: var(--white);
    border-bottom-left-radius: 0;
    border-bottom-right-radius: 0;
  }
  .bag--back .bag__panel {
    height: 572px;
    background: radial-gradient(circle at 52% 50%, var(--cream) 0%, var(--orange-pale) 22%, var(--orange) 70%, var(--orange-deep) 100%);
  }

  .bag__seal {
    position: absolute;
    left: 20px;
    width: 388px;
    height: 2px;
    background: var(--orange-pale);
  }
  .bag--back .bag__seal { background: var(--seal-line); }
  .bag__seal--one { top: 88px; }
  .bag__seal--two { top: 98px; }

  .bag__tab {
    position: absolute;
    left: 92px;
    top: 0;
    width: 244px;
    height: 114px;
    border-radius: 0 0 24px 24px;
    background: linear-gradient(180deg, var(--orange) 0%, var(--orange-deep) 100%);
  }
  .bag__hanger {
    position: absolute;
    left: 164px;
    top: 36px;
    width: 100px;
    height: 20px;
    border-radius: 10px;
    background: var(--white);
  }
  .bag__hanger::before {
    content: "";
    position: absolute;
    left: 40px;
    top: -8px;
    width: 20px;
    height: 20px;
    border-radius: 50%;
    background: var(--white);
  }

  .bag__pattern {
    position: absolute;
    border-radius: 40px;
  }
  .bag--front .bag__pattern {
    left: 36px;
    top: 120px;
    width: 340px;
    height: 420px;
    background: linear-gradient(200deg, rgba(253, 214, 140, 0.75) 0%, rgba(251, 178, 42, 0.35) 45%, rgba(255, 255, 255, 0) 90%);
  }
  .bag--back .bag__pattern {
    left: 230px;
    top: 290px;
    width: 170px;
    height: 240px;
    background: linear-gradient(200deg, rgba(245, 160, 18, 0.55) 0%, rgba(251, 178, 42, 0.25) 60%, rgba(251, 178, 42, 0) 100%);
  }

  .brand {
    position: absolute;
    display: flex;
    align-items: center;
    gap: 14px;
    white-space: nowrap;
  }
  .brand__mark {
    width: 34px;
    height: 34px;
    flex: none;
  }
  .brand__name {
    font-family: "Questrial", sans-serif;
    font-size: 46px;
    line-height: 1;
    letter-spacing: 1px;
  }
  .bag--front .brand { left: 110px; top: 376px; }
  .bag--front .brand__mark { background: var(--orange); }
  .bag--front .brand__name { color: var(--orange); }
  .bag--back .brand { left: 82px; top: 184px; }
  .bag--back .brand__mark { background: var(--white); }
  .bag--back .brand__name { color: var(--white); }

  .tagline {
    position: absolute;
    font-family: "Questrial", sans-serif;
    font-size: 21px;
    line-height: 26px;
    color: var(--ink);
    white-space: nowrap;
  }
  .bag--front .tagline { left: 126px; top: 432px; }
  .bag--back .tagline { left: 100px; top: 244px; }

  .slogan {
    position: absolute;
    left: 0;
    top: 562px;
    width: 428px;
    height: 50px;
    text-align: center;
    font-family: "PT Sans Narrow", sans-serif;
    font-weight: 700;
    font-size: 28px;
    line-height: 50px;
    color: var(--ink);
    white-space: nowrap;
    background: linear-gradient(90deg, var(--orange-deep), #fde7ad 50%, var(--orange-deep));
  }

  .origin {
    position: absolute;
    left: 289px;
    top: 517px;
    font-family: "PT Sans Narrow", sans-serif;
    font-weight: 700;
    font-size: 14px;
    color: var(--ink);
    white-space: nowrap;
  }
  .badges {
    position: absolute;
    left: 262px;
    top: 542px;
    display: flex;
    gap: 16px;
  }
  .badge {
    width: 32px;
    height: 32px;
    border-radius: 50%;
    background: var(--white);
    border: 3px solid var(--orange-pale);
  }
</style>
</head>
<body>

  <section class="bag bag--front" aria-label="Bag front">
    <div class="bag__panel"></div>
    <div class="bag__seal bag__seal--one"></div>
    <div class="bag__seal bag__seal--two"></div>
    <div class="bag__tab"></div>
    <div class="bag__hanger"></div>
    <div class="bag__pattern" role="img" aria-label="Sweeping trail of scattered orange and yellow squares"></div>
    <div class="brand">
      <span class="brand__mark"></span>
      <span class="brand__name">VELORIA</span>
    </div>
    <p class="tagline">Audio and Video Products</p>
    <p class="slogan">For a Pure Connection</p>
  </section>

  <section class="bag bag--back" aria-label="Bag back">
    <div class="bag__panel"></div>
    <div class="bag__seal bag__seal--one"></div>
    <div class="bag__seal bag__seal--two"></div>
    <div class="bag__tab"></div>
    <div class="bag__hanger"></div>
    <div class="bag__pattern" role="img" aria-label="Faint trail of scattered orange squares"></div>
    <div class="brand">
      <span class="brand__mark"></span>
      <span class="brand__name">VELORIA</span>
    </div>
    <p class="tagline">Audio and Video Products</p>
    <p class="origin">MADE IN CHINA</p>
    <div class="badges">
      <span class="badge"></span>
      <span class="badge"></span>
      <span class="badge"></span>
    </div>
  </section>

</body>
</html>
```